At Home Pet Euthanasia - business cards & brand stationary

We already have a logo and the colors and a website. Need a business card designed that will be able to customized to multiple veterinarians who will be partnering with us. The feel needs to be compassionate, comforting with our tagline 'A Gift of Love at Home'. It will be 2 sides.
On the back our platform/partner vets will be customizing each business card with their own service areas, phone numbers, name and title. On the front, i would like to see experimentation with use of our photos, the logo, tagline and a description 'Peaceful and Compassionate At-Home Pet Euthanasia'

```html
<!DOCTYPE html>
<html lang="en">
<head>
<meta charset="utf-8">
<title>Restwell Pet – Business Card</title>
<link rel="stylesheet" href="https://fonts.googleapis.com/css2?family=Arimo:wght@400;700&family=Cormorant+Garamond:ital,wght@1,600&display=swap">
<style>
  :root {
    --backdrop: #a7a7a9;
    --card-white: #ffffff;
    --brand-blue: #7596c2;
    --soft-grey: #e4e4e4;
    --ink: #1a1a1a;
    --band-ink: #1f2f48;
    --photo-warm: #e9a79c;
    --photo-cool: #cfcfd3;
  }
  * { margin: 0; padding: 0; box-sizing: border-box; }
  html, body { width: 1200px; height: 900px; overflow: hidden; }
  body {
    background: var(--backdrop);
    font-family: "Arimo", Arial, sans-serif;
    position: relative;
  }
  .card {
    position: absolute;
    width: 700px;
    height: 400px;
    border-radius: 26px;
    overflow: hidden;
    box-shadow: 0 6px 14px rgba(0,0,0,0.35);
  }

  /* Front */
  .card-front { left: 70px; top: 50px; }
  .front-photo {
    position: absolute; inset: 0;
    background:
      radial-gradient(ellipse at 62% 38%, #b9b5b3 0%, rgba(185,181,179,0) 45%),
      radial-gradient(ellipse at 35% 80%, var(--photo-warm) 0%, rgba(233,167,156,0) 55%),
      linear-gradient(135deg, #9aa4a6 0%, var(--photo-cool) 45%, #ddd9d6 100%);
  }
  .front-description {
    position: absolute;
    left: 110px; right: 30px; bottom: 62px;
    height: 42px;
    padding: 0 20px;
    border-radius: 21px;
    background: var(--brand-blue);
    color: var(--band-ink);
    font-family: "Cormorant Garamond", Georgia, serif;
    font-style: italic;
    font-weight: 600;
    font-size: 21px;
    line-height: 42px;
    letter-spacing: 0.4px;
    white-space: nowrap;
    text-align: center;
    overflow: hidden;
  }

  /* Back */
  .card-back { left: 430px; top: 455px; background: var(--card-white); }
  .back-panel {
    position: absolute;
    right: 0; top: 0; bottom: 0; width: 330px;
    background: var(--soft-grey);
  }
  .brand {
    position: absolute; left: 46px; top: 74px;
    display: flex; align-items: center; gap: 16px;
  }
  .brand-mark {
    width: 62px; height: 62px; border-radius: 50%;
    background: var(--brand-blue);
    flex: none;
  }
  .brand-name {
    font-size: 56px; font-weight: 700; color: var(--brand-blue);
    line-height: 1; white-space: nowrap;
  }
  .brand-tagline {
    position: absolute; left: 126px; top: 152px;
    font-size: 22px; color: var(--brand-blue); letter-spacing: 0.5px;
    white-space: nowrap;
  }
  .contact {
    position: absolute; left: 46px; bottom: 40px;
    color: var(--ink);
  }
  .contact-name { font-size: 30px; color: var(--brand-blue); line-height: 1.05; }
  .contact-title { font-size: 19px; margin-bottom: 14px; }
  .contact-line {
    display: flex; align-items: center; gap: 10px;
    font-size: 19px; line-height: 1.45; white-space: nowrap;
  }
  .contact-line svg { width: 18px; height: 18px; flex: none; }
  .accent { color: var(--brand-blue); }
  .address {
    position: absolute; right: 36px; top: 200px;
    text-align: right; font-size: 18px; line-height: 1.35; color: var(--ink);
    white-space: nowrap;
  }
</style>
</head>
<body>

<section class="card card-front">
  <div class="front-photo" role="img" aria-label="Photograph of a girl lovingly hugging a blue-eyed tabby cat"></div>
  <p class="front-description">Peaceful and Compassionate At-Home Pet Euthanasia</p>
</section>

<section class="card card-back">
  <div class="back-panel"></div>

  <div class="brand">
    <span class="brand-mark"></span>
    <span class="brand-name">Restwell Pet</span>
  </div>
  <p class="brand-tagline">A gift of love at home.</p>

  <div class="contact">
    <p class="contact-name">Daniel Hart</p>
    <p class="contact-title">Managing Director</p>
    <p class="contact-line">
      <svg viewBox="0 0 24 24" aria-hidden="true"><path fill="#7596c2" d="M6.6 10.8a15 15 0 0 0 6.6 6.6l2.2-2.2a1 1 0 0 1 1-.25 11.4 11.4 0 0 0 3.6.57 1 1 0 0 1 1 1V20a1 1 0 0 1-1 1A17 17 0 0 1 3 4a1 1 0 0 1 1-1h3.5a1 1 0 0 1 1 1c0 1.25.2 2.45.57 3.57a1 1 0 0 1-.25 1z"/></svg>
      044-987 654 321
    </p>
    <p class="contact-line">
      <svg viewBox="0 0 24 24" aria-hidden="true"><rect x="2" y="5" width="20" height="14" rx="1.5" fill="#7596c2"/><path d="M3 6l9 7 9-7" fill="none" stroke="#fff" stroke-width="1.6"/></svg>
      info@restwellpet.com
    </p>
    <p class="contact-line">
      <svg viewBox="0 0 24 24" aria-hidden="true"><g fill="none" stroke="#7596c2" stroke-width="1.6"><circle cx="12" cy="12" r="9"/><ellipse cx="12" cy="12" rx="4" ry="9"/><path d="M3 12h18M5 7h14M5 17h14"/></g></svg>
      <span>www.<span class="accent">restwellpet</span>.com</span>
    </p>
  </div>

  <p class="address">421, Address line goes here<br>45452, Country Name</p>
</section>

</body>
</html>
```